Wandering Rooms Stationary Set

Wandering Rooms is a bespoke interior design firm set to provide services to VIP clients with elegance and minimalism is the main theme for our stationary set. We require a full stationary set covering A4 letterhead, A4 & A3 envelopes, business cards, USB's, CDs, email signature and any other item the designer sees fit. logo is already designed and finalized, and we require the designer to use it as is without modifying the logo.

Address to be used on letterhead / business cards ...etc shall be as follows:

Phone : +971 2 518 2047
P.O. Box : 309186
Address: Block C&D, Bldg. 47, Court 12, Abu Dhabi, United Arab Emirates
Website: www.wanderingrooms-example.com

Target Market(s)

VIP Clients

Industry/Entity Type

Interior Design

Font styles to use
Other font styles liked:
• something to be unique

Colors

Designer to choose colors to be used in the design.

Requirements
Must have
• Elegant, minimalistic
Nice to have
• Simple yet elegant design having a sharp yet clean cut format
Should not have
• No additional colours, just colours that are used in the logo (silver, black or gold)

```html
<!DOCTYPE html>
<html lang="en">
<head>
<meta charset="utf-8">
<title>Wandering Rooms — Business Cards</title>
<link href="https://fonts.googleapis.com/css2?family=Cormorant+Garamond:wght@400;500&family=Great+Vibes&display=swap" rel="stylesheet">
<style>
  :root {
    --bg: #1e1e1f;
    --card-dark: #373738;
    --silver: #d9d9d9;
    --gold: #b5975a;
    --white: #ffffff;
    --ink: #4a4a4a;
  }
  * { margin: 0; padding: 0; box-sizing: border-box; }
  html, body { width: 1200px; height: 960px; overflow: hidden; background: var(--bg); }
  .stage { position: relative; width: 1200px; height: 960px; }
  .card {
    position: absolute; left: 250px; width: 700px; height: 400px; overflow: hidden;
    box-shadow: 0 8px 24px rgba(0,0,0,.45);
  }
  .card-back { top: 50px; background: var(--card-dark); }
  .card-front { top: 500px; background: var(--white); }

  .brand {
    position: absolute; font-family: "Cormorant Garamond", serif; font-weight: 500;
    text-transform: uppercase; white-space: nowrap;
  }
  .card-back .brand { left: 0; right: 0; top: 170px; text-align: center; font-size: 40px; letter-spacing: 6px; color: var(--silver); }
  .card-front .brand { left: 56px; top: 76px; font-size: 28px; letter-spacing: 5px; color: var(--gold); }

  .gold-panel { position: absolute; inset: 0; }

  .contact {
    position: absolute; left: 56px; top: 218px;
    font-family: "Cormorant Garamond", serif; font-size: 17px; line-height: 22px; color: var(--ink);
  }
  .contact .address { margin-bottom: 14px; }
  .contact-line { display: flex; align-items: center; gap: 10px; }
  .contact-line svg { width: 12px; height: 12px; flex: none; }

  .holder { position: absolute; right: 36px; bottom: 112px; text-align: right; color: var(--white); white-space: nowrap; }
  .holder-name { font-family: "Great Vibes", cursive; font-size: 27px; line-height: 1; }
  .holder-title { font-family: "Cormorant Garamond", serif; font-size: 17px; }
</style>
</head>
<body>
<main class="stage">
  <section class="card card-back">
    <div class="brand">Wandering Rooms</div>
  </section>

  <section class="card card-front">
    <svg class="gold-panel" viewBox="0 0 700 400" aria-hidden="true">
      <path d="M400 0 C 480 100, 490 260, 390 400 L700 400 L700 0 Z" fill="var(--gold)"/>
      <path d="M416 0 C 500 105, 506 265, 410 400" fill="none" stroke="var(--white)" stroke-width="3"/>
    </svg>

    <div class="brand">Wandering Rooms</div>

    <div class="contact">
      <p class="address">P.O. Box : 309186,<br>Block C&amp;D, Bldg. 47, Court 12<br>Abu Dhabi, United Arab Emirate</p>
      <p class="contact-line">
        <svg viewBox="0 0 12 12"><path d="M2 1 L4 1 L5 3.5 L3.8 4.5 C4.5 6 6 7.5 7.5 8.2 L8.5 7 L11 8 L11 10 C11 10.6 10.5 11 10 11 C5 11 1 7 1 2 C1 1.5 1.4 1 2 1 Z" fill="var(--gold)"/></svg>
        +971 2 518 2047</p>
      <p class="contact-line">
        <svg viewBox="0 0 12 12"><rect x="0.5" y="2" width="11" height="8" fill="var(--gold)"/><path d="M0.5 2 L6 6.5 L11.5 2" fill="none" stroke="var(--white)" stroke-width="1"/></svg>
        info@wanderingrooms-example.com</p>
      <p class="contact-line">
        <svg viewBox="0 0 12 12"><circle cx="6" cy="6" r="5.5" fill="var(--gold)"/><path d="M0.5 6 H11.5 M6 0.5 C3.5 3 3.5 9 6 11.5 M6 0.5 C8.5 3 8.5 9 6 11.5" fill="none" stroke="var(--white)" stroke-width="0.7"/></svg>
        www.wanderingrooms-example.com</p>
    </div>

    <div class="holder">
      <p class="holder-name">Daniel Hartley</p>
      <p class="holder-title">President</p>
    </div>
  </section>
</main>
</body>
</html>
```